Flyer Design Project

We need a flyer design for a 1 year old domestic cleaning company based in Wiltshire, England. We provide households with high quality, hard working cleaners. We would like to see designs which use blue (the colour on the logo attatched). The final design should communicate a clean, premier and thorough service in a clear and bold way. We would like the flyer to be A5 with a single sided design. We have attached an A5 word document with the words we would like to be used in the design, what we need is for you to give it some life, colour, artwork and a professional touch. We are perfectionsists which we would like to illustrate to our customer through this flyer.
Updates

payment has been guaranteed!

Sorry..... please no pictures of females on the designs. many thanks

Target Market(s)

females with higher than average income, aged 30-50. Have families and work 9-5.

Industry/Entity Type

It Company

Requirements
Must have
• The flyer must include the logo attatched and the words in the A5 document attatched. With RELIABLE CLEANERS preferably the headline. A5 - single sided.
The Flyer must also include our introductory offer.....
First Clean FREE
Allow us to demonstrate our standards

this should be emphasised.

PLEASE NOTE: can this be added to the list of words on the flyer please:

Ironing service - one day turn around
Nice to have
• some pictures - nothing cheesey. Again, pictures should communicate our modern professional approach.

```html
<!DOCTYPE html>
<html lang="en">
<head>
<meta charset="UTF-8">
<title>Brightwell Cleaners – Flyer</title>
<link href="https://fonts.googleapis.com/css2?family=Roboto+Condensed:wght@400;500;700&family=Oswald:wght@600&family=Roboto:wght@400;500;700&display=swap" rel="stylesheet">
<style>
  :root {
    --brand-blue: #1f4fbf;
    --band-dark: #1560c8;
    --band-light: #4aa3f0;
    --badge-blue: #3b93e8;
    --ink: #1b1f3b;
    --dot: #2a66d6;
    --sky-top: #eaf6fd;
    --sky-mid: #a9ddf7;
    --sky-low: #3ea2ea;
    --white: #ffffff;
  }
  * { margin: 0; padding: 0; box-sizing: border-box; }
  html, body { width: 846px; height: 1200px; overflow: hidden; }
  body { font-family: "Roboto Condensed", Arial, sans-serif; }

  .flyer {
    position: relative;
    width: 846px;
    height: 1200px;
    overflow: hidden;
    background: linear-gradient(180deg, var(--white) 0%, var(--white) 18%, var(--sky-top) 40%, var(--sky-mid) 62%, var(--sky-low) 100%);
  }

  .brand { position: absolute; left: 84px; top: 82px; }
  .brand-name {
    display: flex; align-items: center; gap: 14px;
    font-family: "Roboto", Arial, sans-serif;
    font-weight: 500; font-size: 42px; color: var(--brand-blue);
  }
  .brand-mark { width: 30px; height: 30px; background: var(--brand-blue); }
  .brand-tagline {
    margin: 12px 0 0 70px;
    font-family: "Roboto", Arial, sans-serif;
    font-weight: 700; font-size: 18px; color: var(--ink);
  }

  .headline-band {
    position: absolute; left: 0; top: 240px;
    width: 580px; height: 100px;
    background: linear-gradient(90deg, var(--band-dark) 0%, var(--band-light) 100%);
    display: flex; align-items: center; padding-left: 18px;
  }
  .headline {
    font-family: "Oswald", "Roboto Condensed", sans-serif;
    font-weight: 600; font-size: 56px; color: var(--white);
    letter-spacing: 0.5px;
  }

  .offer-badge { position: absolute; left: 562px; top: 118px; width: 286px; height: 286px; }
  .offer-badge svg { position: absolute; inset: 0; }
  .offer-text {
    position: absolute; inset: 0;
    display: flex; flex-direction: column; align-items: center; justify-content: center;
    color: var(--white); text-align: center;
    font-family: "Roboto", Arial, sans-serif;
  }
  .offer-lead { font-size: 36px; font-weight: 400; }
  .offer-free { font-size: 66px; font-weight: 700; line-height: 1; margin: 4px 0 8px; }
  .offer-note { font-size: 21px; line-height: 1.2; }

  .benefits {
    position: absolute; left: 56px; top: 358px;
    list-style: none;
  }
  .benefits li {
    display: flex; align-items: center;
    height: 58px;
    font-size: 33px; font-weight: 500; color: var(--ink);
  }
  .benefits li::before {
    content: ""; width: 12px; height: 12px; border-radius: 50%;
    background: var(--dot); margin-right: 14px; flex-shrink: 0;
  }

  .contact { position: absolute; left: 80px; top: 800px; color: var(--white); }
  .contact-phone { font-family: "Roboto", Arial, sans-serif; font-size: 44px; font-weight: 400; }
  .contact-email { font-family: "Roboto", Arial, sans-serif; font-size: 20px; margin-top: 18px; }

  .sponges-visual {
    position: absolute; left: 470px; top: 690px; width: 376px; height: 510px;
    background: linear-gradient(160deg, #8ad04a 0%, #ef7a3c 35%, #6a48d6 60%, #2f86e0 85%, #7ed04a 100%);
    clip-path: polygon(40% 0, 100% 0, 100% 100%, 5% 100%, 0 55%);
    opacity: 0.9;
  }
  .supplies-visual {
    position: absolute; left: 0; top: 916px; width: 440px; height: 284px;
    background: linear-gradient(120deg, #f1e24a 0%, #9fcde8 45%, #c9d4dc 100%);
    clip-path: polygon(0 20%, 40% 10%, 95% 40%, 100% 100%, 0 100%);
    opacity: 0.85;
  }
</style>
</head>
<body>
<main class="flyer">
  <header class="brand">
    <div class="brand-name"><span class="brand-mark"></span>Brightwell Cleaners</div>
    <p class="brand-tagline">Premier Domestic Cleaners</p>
  </header>

  <div class="headline-band"><h1 class="headline">RELIABLE CLEANERS!</h1></div>

  <aside class="offer-badge">
    <svg viewBox="0 0 286 286" aria-hidden="true">
      <path fill="var(--badge-blue)" d="
        M143 6
        C160 6 168 20 183 24 C198 28 212 20 226 30 C240 40 236 56 246 68
        C256 80 272 84 276 100 C280 116 268 128 270 143
        C272 158 284 170 278 186 C272 202 256 204 248 218
        C240 232 242 248 228 258 C214 268 200 260 184 264
        C168 268 158 280 143 280 C128 280 118 268 102 264
        C86 260 72 268 58 258 C44 248 46 232 38 218
        C30 204 14 202 8 186 C2 170 14 158 16 143
        C18 128 6 116 10 100 C14 84 30 80 40 68
        C50 56 46 40 60 30 C74 20 88 28 103 24
        C118 20 126 6 143 6 Z"/>
    </svg>
    <div class="offer-text">
      <span class="offer-lead">First Clean</span>
      <strong class="offer-free">FREE</strong>
      <span class="offer-note">Allow us to demonstrate<br>our standards...</span>
    </div>
  </aside>

  <ul class="benefits">
    <li>Personalised Service</li>
    <li>Constantly Thorough</li>
    <li>Hassel Free</li>
    <li>Insured</li>
    <li>Regular Weekly Cleans</li>
    <li>No Contracts</li>
    <li>Ironing Service - One day turn around</li>
  </ul>

  <div class="sponges-visual" role="img" aria-label="Photo of a stack of colourful cleaning sponges"></div>
  <div class="supplies-visual" role="img" aria-label="Photo of a bucket and box of cleaning supplies with gloves and spray bottles"></div>

  <section class="contact">
    <p class="contact-phone">Tele: 07700900417</p>
    <p class="contact-email">Email: brightwellcleaners@example.co.uk</p>
  </section>
</main>
</body>
</html>
```